Larkmoor Drones Business Card

We are a new company based in Central Queensland, Australia that uses specalised drones (Voskel Ferra Q80) to undertake mainly agricultural operations, like spraying weeds, spraying crops, spreading seed etc. I have attached a Plimbo proof of a card I was thinking along the lines of - purely a start point. The drone used in the business card MUST be a Voskel Ferra Q80.
I am very open to other ideas, especially fonts and layout. I don't have website etc set up yet.
The images are stock and easily interchangeable, I just ask that any background images reflect the local central Queensland area. The photo of the drone is not even complete (propellers cut off) and I need a new stock photo – I’m not sure if this is an issue, or I can pay for an image if need be. PLEASE FIND AN FERRA Q80 image - 4 sprayers, not 6.
The logo/business name is very draft and looking for further ideas, ideally incorporating drones or agriculture design elements into the design of the business name. The business name needs work on the graphic/design – it is a draft that I have included, the drone propellers (being a different colour) are DRAFT only and intended for changes. PLEASE DO NOT USE THE DRONE PORPELLER I HAVE USED AS A DRAFT. TRY TO FIND SOMETHING ELSE.. The arrow is a shape and not aligned in any way, I would also like ideas on different fonts and additional elements, like air streams, aviation elements, aviation or country western (farming like) themes and fonts etc.
Ideally looking at staying within the blue, green and yellow colours, keeping with an natural, outdoorsy, environmental feel.

Target Market(s)

Farmers, Agriculture, Local Governments, Land Managers

Industry/Entity Type

Agriculture, Drones, Aviation

Contact Information for Business Card

Agricultural Drone (Voskel Ferra Q80), Farming, Business Name.

Font styles to use
Sans Serif

Colors
0054AA
0677BA
7BADD7
CADEEF
E8F1F8
0094D4
00A9DD
6FCCEA
C7EBF8
E9F6FB
00AB8E
00BBA5
67D7C9
C6EFE9
E9F9F6
59FF00
82FF00
B8FF75
E3FFCB
F4FFEA

Requirements
Must have
• Voskel Ferra Q80 Drone
Should not have
• Tractors

```html
<!DOCTYPE html>
<html lang="en">
<head>
<meta charset="utf-8">
<title>Larkmoor Drones Business Card</title>
<link rel="stylesheet" href="https://fonts.googleapis.com/css2?family=Alfa+Slab+One&family=Lilita+One&family=Cutive&display=swap">
<style>
  :root {
    --bg: #232323;
    --green: #7e8f3c;
    --green-deep: #6f8034;
    --blue: #4a5a76;
    --white: #ffffff;
    --sky-top: #f3b54a;
    --sky-mid: #f0c878;
    --field: #8aa13a;
    --field-deep: #55702a;
    --ink: #1f2a14;
  }
  * { box-sizing: border-box; margin: 0; padding: 0; }
  html, body { width: 1200px; height: 800px; overflow: hidden; background: var(--bg); }
  .stage {
    width: 1200px; height: 800px;
    display: flex; align-items: center; justify-content: center; gap: 40px;
  }
  .card {
    position: relative; width: 560px; height: 320px;
    border-radius: 22px; overflow: hidden; background: var(--white);
  }

  /* Front */
  .card-front { background: var(--green); }
  .front-photo {
    position: absolute; left: 0; top: 0; width: 100%; height: 210px;
    background: linear-gradient(180deg, var(--sky-top) 0%, var(--sky-mid) 35%, var(--field) 62%, var(--field-deep) 100%);
  }
  .front-band {
    position: absolute; left: 0; top: 210px; width: 100%; height: 34px; background: var(--blue);
  }
  .services {
    position: absolute; left: 0; right: 0; top: 26px; text-align: center;
    font-family: "Alfa Slab One", serif; font-size: 22px; letter-spacing: 4px; color: var(--blue);
  }
  .brand {
    position: absolute; right: 34px; text-align: right; color: var(--white);
    font-family: "Lilita One", sans-serif; line-height: 1; letter-spacing: 1px;
  }
  .card-front .brand { top: 214px; font-size: 28px; }
  .tagline {
    position: absolute; font-family: "Cutive", serif; letter-spacing: 1px; color: var(--ink);
  }
  .card-front .tagline { right: 34px; top: 262px; font-size: 13px; }

  /* Back */
  .back-art { position: absolute; inset: 0; }
  .holder { position: absolute; left: 30px; top: 40px; color: var(--white); font-family: "Lilita One", sans-serif; }
  .holder-name { font-size: 36px; line-height: 1; letter-spacing: 0.5px; }
  .holder-role { font-size: 17px; margin-top: 4px; }
  .contacts {
    position: absolute; right: 24px; top: 146px; list-style: none;
    font-family: "Lilita One", sans-serif; color: var(--white); font-size: 14px;
  }
  .contacts li { display: flex; align-items: center; justify-content: flex-end; gap: 8px; height: 22px; }
  .contact-icon { width: 16px; height: 16px; flex: none; }
  .card-back .brand { left: 30px; right: auto; text-align: left; top: 256px; font-size: 26px; }
  .card-back .tagline { left: 32px; top: 286px; font-size: 11px; color: var(--white); }
</style>
</head>
<body>
<main class="stage">

  <section class="card card-front" aria-label="Business card front">
    <div class="front-photo" role="img" aria-label="Photo of a Voskel Ferra Q80 agricultural drone spraying a green Central Queensland field at sunset"></div>
    <div class="front-band"></div>
    <p class="services">SPRAY · WEED · SEED · FEED</p>
    <p class="brand">LARKMOOR DRONES</p>
    <p class="tagline">SERVICING CENTRAL QUEENSLAND</p>
  </section>

  <section class="card card-back" aria-label="Business card back">
    <svg class="back-art" viewBox="0 0 560 320" aria-hidden="true">
      <defs>
        <linearGradient id="meadow" x1="0" y1="0" x2="0" y2="1">
          <stop offset="0.28" stop-color="#ffffff"/>
          <stop offset="0.55" stop-color="#a8b67a"/>
          <stop offset="0.75" stop-color="#7e8f3c"/>
          <stop offset="1" stop-color="#7e8f3c"/>
        </linearGradient>
      </defs>
      <rect class="meadow" width="560" height="320" fill="url(#meadow)"/>
      <path class="blue-sweep" d="M0 250 C120 240 220 215 300 140 C370 70 430 30 560 28 V0 H0 Z" fill="var(--blue)"/>
      <path class="green-sweep" d="M0 215 C110 212 200 190 270 130 C340 65 410 26 560 18 V0 H0 Z" fill="var(--green)"/>
      <path class="white-stream" d="M0 220 C110 217 205 195 275 134 C345 70 412 32 560 22" fill="none" stroke="#ffffff" stroke-width="4"/>
      <path class="green-stream" d="M300 180 C330 120 380 60 520 30 C420 50 360 90 300 180 Z" fill="var(--green)"/>
    </svg>

    <div class="holder">
      <p class="holder-name">Maren Vostrik</p>
      <p class="holder-role">Founder &amp; CEO</p>
    </div>

    <ul class="contacts">
      <li>(555) 014-2290
        <svg class="contact-icon" viewBox="0 0 16 16"><circle cx="8" cy="8" r="8" fill="#fff"/><path d="M5 4.5l1.6-.4 1 2-1 .8a5 5 0 0 0 2.5 2.5l.8-1 2 1-.4 1.6C8 11.5 4.5 8 5 4.5z" fill="var(--green-deep)"/></svg></li>
      <li>www.larkmoordrones.example
        <svg class="contact-icon" viewBox="0 0 16 16"><circle cx="8" cy="8" r="8" fill="#fff"/><circle cx="8" cy="8" r="4.5" fill="none" stroke="var(--green-deep)" stroke-width="1.2"/><path d="M3.5 8h9M8 3.5c-2 2.5-2 6.5 0 9M8 3.5c2 2.5 2 6.5 0 9" fill="none" stroke="var(--green-deep)" stroke-width="1"/></svg></li>
      <li>info@larkmoordrones.example
        <svg class="contact-icon" viewBox="0 0 16 16"><circle cx="8" cy="8" r="8" fill="#fff"/><rect x="4" y="5" width="8" height="6" fill="none" stroke="var(--green-deep)" stroke-width="1.2"/><path d="M4 5l4 3.5L12 5" fill="none" stroke="var(--green-deep)" stroke-width="1.2"/></svg></li>
      <li>@larkmoordrones
        <svg class="contact-icon" viewBox="0 0 16 16"><circle cx="8" cy="8" r="8" fill="#fff"/></svg></li>
      <li>@larkmoordrones
        <svg class="contact-icon" viewBox="0 0 16 16"><circle cx="8" cy="8" r="8" fill="#fff"/></svg></li>
    </ul>

    <p class="brand">LARKMOOR DRONES</p>
    <p class="tagline">SERVICING CENTRAL QUEENSLAND</p>
  </section>

</main>
</body>
</html>
```